Occasions chocolate packaging

We are looking for 7 packaging designs for bars of chocolate.

Each design needs to be different and we’re not looking for a consistent brand or branding message across the designs. Inspiration should come from gift/occasion cards. Fun, simple, bold, vibrant colours and eye catching, i.e. not vintage or just text.

The front of the packaging should have the main message on and is free of any branding. You don’t need to design the back, just simply allow the main background colour or design pattern to continue around.

These are the different designs we are after, I’ve added in some text for each to give you some guidance but feel free to play around with the message if it suits the design better.

1) Mum
‘The best mum’, ‘Best mum in the World’, ‘Number 1 Mum’

2) Dad
‘The Best Dad’, ‘Best Dad Ever’, ‘Number 1 Dad’, ‘You’re my hero Dad’

3) Husband
‘Best Husband in the World’, ‘Husband I Love You’, ‘Darling Husband’

4) Wife
‘Best Wife in the World’, ‘For my Wonderful Wife’, ‘My Beautiful Wife’

5) Congratulations
Simple one, just Congratulations

6) Thinking of you
Try and keep this neutral as it could be used for happy and sad situations.

7) Thank you
Keep this gender neutral.

Sides:
The sides need to have the following text:

FINE BELGIAN DARK CHOCOLATE
infused with Orange

Back:
The main colour of the front should continue all the way around, we will place a box with the contents and bar code on here ourselves so no need to do anything.

Dimensions:
Attached in the document, front of package is 85mm by 190mm.

The packaging is made from folded card, the first blank part is for gluing the back on to.

Reason: I'm extending the deadline as I've only received 1 design so far which has followed the brief. Although I do like it, I would like to see at least some competition...

```html
<!DOCTYPE html>
<html lang="en">
<head>
<meta charset="utf-8">
<title>Congratulations – Chocolate Bar Wrap</title>
<link href="https://fonts.googleapis.com/css2?family=Oswald:wght@700&family=Open+Sans:ital,wght@1,600;1,700&display=swap" rel="stylesheet">
<style>
  :root {
    --stage: #e8e9eb;
    --wrap-red: #cf1a24;
    --wrap-red-deep: #a80f18;
    --wrap-red-light: #e3262f;
    --stripe: rgba(140, 0, 10, 0.22);
    --ink-white: #ffffff;
  }
  html, body {
    margin: 0;
    padding: 0;
    width: 1200px;
    height: 960px;
    overflow: hidden;
    background: var(--stage);
  }
  .canvas {
    position: relative;
    width: 1200px;
    height: 960px;
  }
  .wrap {
    position: absolute;
    left: 382px;
    top: 50px;
    width: 435px;
    height: 860px;
    box-shadow: 0 10px 30px rgba(0,0,0,0.18);
  }
  .wrap svg { display: block; }
  .headline {
    font-family: "Oswald", "Arial Narrow", sans-serif;
    font-weight: 700;
    fill: var(--ink-white);
  }
  .side-title {
    font-family: "Open Sans", Arial, sans-serif;
    font-style: italic;
    font-weight: 700;
    fill: var(--ink-white);
    letter-spacing: 2.5px;
  }
  .side-sub {
    font-family: "Open Sans", Arial, sans-serif;
    font-style: italic;
    font-weight: 600;
    fill: var(--ink-white);
    letter-spacing: 1.5px;
  }
  .sparkle-dot { fill: var(--ink-white); }
  .sparkle-star { fill: var(--ink-white); }
</style>
</head>
<body>
<div class="canvas">
  <div class="wrap">
    <svg width="435" height="860" viewBox="0 0 435 860" xmlns="http://www.w3.org/2000/svg">
      <defs>
        <radialGradient id="front-glow" cx="0.5" cy="0.45" r="0.75">
          <stop offset="0" stop-color="var(--wrap-red-light)"/>
          <stop offset="1" stop-color="var(--wrap-red)"/>
        </radialGradient>
        <pattern id="diagonal-stripes" width="14" height="14" patternUnits="userSpaceOnUse" patternTransform="rotate(-45)">
          <rect x="0" y="0" width="7" height="14" fill="var(--stripe)"/>
        </pattern>
        <radialGradient id="dot-glow">
          <stop offset="0" stop-color="#ffffff" stop-opacity="0.95"/>
          <stop offset="1" stop-color="#ffffff" stop-opacity="0"/>
        </radialGradient>
        <linearGradient id="art-tone" x1="0" y1="0" x2="0" y2="1">
          <stop offset="0" stop-color="#ffffff" stop-opacity="0.55"/>
          <stop offset="1" stop-color="#ffffff" stop-opacity="0.9"/>
        </linearGradient>
        <symbol id="star" viewBox="-10 -10 20 20">
          <path d="M0 -10 L1.6 -1.6 L10 0 L1.6 1.6 L0 10 L-1.6 1.6 L-10 0 L-1.6 -1.6 Z"/>
        </symbol>
      </defs>

      <!-- side panel -->
      <g class="side-panel">
        <rect x="0" y="0" width="50" height="860" fill="var(--wrap-red-deep)"/>
        <rect x="0" y="0" width="50" height="860" fill="url(#diagonal-stripes)"/>
        <g transform="translate(31 842) rotate(-90)">
          <text class="side-title" x="0" y="0" font-size="15">FINE BELGIAN DARK CHOCOLATE</text>
          <text class="side-sub" x="822" y="0" font-size="14" text-anchor="end">infused with Orange</text>
        </g>
      </g>

      <!-- front panel -->
      <g class="front-panel" transform="translate(50 0)">
        <rect x="0" y="0" width="385" height="860" fill="url(#front-glow)"/>
        <rect x="0" y="0" width="385" height="860" fill="url(#diagonal-stripes)"/>

        <g class="sparkles">
          <circle class="sparkle-dot" cx="40" cy="22" r="6" fill="url(#dot-glow)"/>
          <circle cx="175" cy="110" r="7" fill="url(#dot-glow)"/>
          <circle cx="250" cy="70" r="5" fill="url(#dot-glow)"/>
          <circle cx="340" cy="30" r="6" fill="url(#dot-glow)"/>
          <circle cx="360" cy="150" r="5" fill="url(#dot-glow)"/>
          <circle cx="185" cy="300" r="6" fill="url(#dot-glow)"/>
          <circle cx="350" cy="300" r="7" fill="url(#dot-glow)"/>
          <circle cx="180" cy="470" r="5" fill="url(#dot-glow)"/>
          <circle cx="365" cy="520" r="6" fill="url(#dot-glow)"/>
          <circle cx="170" cy="640" r="7" fill="url(#dot-glow)"/>
          <circle cx="320" cy="610" r="5" fill="url(#dot-glow)"/>
          <circle cx="300" cy="790" r="7" fill="url(#dot-glow)"/>
          <circle cx="370" cy="700" r="5" fill="url(#dot-glow)"/>
          <circle cx="190" cy="830" r="6" fill="url(#dot-glow)"/>
          <circle cx="60" cy="850" r="7" fill="url(#dot-glow)"/>
          <circle cx="355" cy="820" r="6" fill="url(#dot-glow)"/>
          <use href="#star" class="sparkle-star" x="148" y="112" width="14" height="14"/>
          <use href="#star" class="sparkle-star" x="280" y="100" width="12" height="12"/>
          <use href="#star" class="sparkle-star" x="185" y="230" width="12" height="12"/>
          <use href="#star" class="sparkle-star" x="172" y="400" width="10" height="10"/>
          <use href="#star" class="sparkle-star" x="345" y="430" width="12" height="12"/>
          <use href="#star" class="sparkle-star" x="200" y="560" width="12" height="12"/>
          <use href="#star" class="sparkle-star" x="345" y="620" width="14" height="14"/>
          <use href="#star" class="sparkle-star" x="355" y="740" width="14" height="14"/>
          <use href="#star" class="sparkle-star" x="260" y="765" width="10" height="10"/>
          <use href="#star" class="sparkle-star" x="245" y="842" width="10" height="10"/>
          <use href="#star" class="sparkle-star" x="20" y="770" width="10" height="10"/>
        </g>

        <g transform="translate(158 828) rotate(-90)">
          <text class="headline" x="0" y="0" font-size="120" textLength="790" lengthAdjust="spacingAndGlyphs">CONGRATULATIONS</text>
        </g>

        <rect class="trophy-art" role="img" aria-label="White silhouette of a cheering figure standing on a winner's trophy cup"
              x="178" y="100" width="186" height="650" rx="30" fill="url(#art-tone)"/>
      </g>
    </svg>
  </div>
</div>
</body>
</html>
```